Business Card Design Project

Looking to update our business cards. We have a logo with our slogan. We are an IT firm so we wouldlike a modern look.

Industry/Entity Type

Business

```html
<!DOCTYPE html>
<html lang="en">
<head>
<meta charset="utf-8">
<title>Kernova Business Cards</title>
<link rel="stylesheet" href="https://fonts.googleapis.com/css2?family=Jost:wght@400;500;600&display=swap">
<style>
  :root {
    --stage: #5b3b24;
    --card-white: #ffffff;
    --brand-dark: #6a7d3c;
    --brand-light: #b0c244;
    --ink: #2f2f2f;
    --ink-soft: #3c3c3c;
    --label: #1e1208;
    --tech-deep: #14264f;
    --tech-mid: #2f63b8;
    --tech-glow: #dfeafc;
  }
  * { box-sizing: border-box; margin: 0; padding: 0; }
  html, body { width: 1200px; height: 788px; overflow: hidden; }
  body {
    position: relative;
    background: var(--stage);
    font-family: "Jost", sans-serif;
  }
  .view-label {
    position: absolute;
    width: 525px;
    text-align: center;
    font-size: 22px;
    font-weight: 400;
    color: var(--label);
    opacity: .85;
  }
  .card {
    position: absolute;
    width: 525px;
    height: 298px;
    border-radius: 22px;
    overflow: hidden;
    background: var(--card-white);
  }
  .card--front { left: 50px; top: 80px; }
  .card--back-white { left: 620px; top: 80px; }
  .card--back-green { left: 50px; top: 455px; background: var(--brand-light); }
  .card--back-tech { left: 620px; top: 455px; }

  .tech-backdrop {
    position: absolute; inset: 0;
    background:
      radial-gradient(ellipse 45% 55% at 58% 52%, var(--tech-glow) 0%, rgba(160,190,240,.75) 35%, rgba(47,99,184,0) 75%),
      linear-gradient(180deg, var(--tech-mid) 0%, var(--tech-deep) 100%);
  }

  .wordmark {
    position: absolute;
    left: 0; right: 0;
    text-align: center;
    color: var(--brand-dark);
  }
  .wordmark__name {
    display: block;
    font-weight: 600;
    letter-spacing: .16em;
    line-height: 1;
  }
  .wordmark__tagline {
    display: block;
    font-weight: 600;
    letter-spacing: .2em;
    color: var(--ink);
  }
  .wordmark--small { top: 60px; }
  .wordmark--small .wordmark__name { font-size: 40px; }
  .wordmark--small .wordmark__tagline { font-size: 9.5px; margin-top: 8px; }
  .wordmark--large { top: 118px; }
  .wordmark--large .wordmark__name { font-size: 56px; }
  .wordmark--large .wordmark__tagline { font-size: 13px; margin-top: 12px; }

  .name-band {
    position: absolute; top: 147px; left: 0;
    width: 450px; height: 33px;
    background: var(--brand-dark);
    color: #fff;
    font-size: 18px;
    line-height: 33px;
    text-align: center;
  }
  .name-band__role { font-size: 14px; }
  .name-band-accent {
    position: absolute; top: 147px; left: 459px;
    width: 66px; height: 33px;
    background: var(--brand-light);
  }

  .contact-list {
    position: absolute; left: 69px; top: 200px;
    list-style: none;
    font-size: 13.5px;
    color: var(--ink-soft);
  }
  .contact-list li {
    display: flex; align-items: center;
    height: 22px;
  }
  .contact-list svg { width: 12px; height: 12px; margin-right: 8px; fill: var(--ink-soft); }
  .address {
    position: absolute; left: 263px; top: 232px;
    font-style: normal;
    font-size: 13px;
    line-height: 17.5px;
    color: var(--ink-soft);
  }
</style>
</head>
<body>
  <div class="view-label" style="left:50px; top:33px;">Front</div>
  <div class="view-label" style="left:620px; top:33px;">Back - 1</div>
  <div class="view-label" style="left:50px; top:403px;">Back - 2</div>
  <div class="view-label" style="left:620px; top:403px;">Back - 3</div>

  <section class="card card--front">
    <div class="wordmark wordmark--small">
      <span class="wordmark__name">KERNOVA</span>
      <span class="wordmark__tagline">MAKING TECH CALM</span>
    </div>
    <div class="name-band">Your Name, <span class="name-band__role">Designation</span></div>
    <div class="name-band-accent"></div>
    <ul class="contact-list">
      <li><svg viewBox="0 0 12 12"><circle cx="6" cy="6" r="5.5" fill="none" stroke="#3c3c3c"/><path d="M4 3.2l1 1.3-.6.8c.5 1 1.2 1.7 2.2 2.2l.8-.6 1.3 1-.6 1C5.6 8.6 3.4 6.4 3 4z"/></svg>+12 345 67890</li>
      <li><svg viewBox="0 0 12 12"><path d="M2 5l1.2-3h5.6L10 5h1v4H10v1.5H8.5V9h-5v1.5H2V9H1V5zM3.2 5h5.6L8 3H4z"/></svg>+12 345 67890</li>
      <li><svg viewBox="0 0 12 12"><path d="M1 4l5-3 5 3v6H1zM2 4.6L6 7l4-2.4L6 2.2z"/></svg>info@website.com</li>
      <li><svg viewBox="0 0 12 12"><circle cx="6" cy="6" r="5" fill="none" stroke="#3c3c3c"/><ellipse cx="6" cy="6" rx="2" ry="5" fill="none" stroke="#3c3c3c"/><path d="M1 6h10" stroke="#3c3c3c"/></svg>www.website.com</li>
    </ul>
    <address class="address">#0000, Street Name<br>Area Name<br>Country Code</address>
  </section>

  <section class="card card--back-white">
    <div class="wordmark wordmark--large">
      <span class="wordmark__name">KERNOVA</span>
      <span class="wordmark__tagline">MAKING TECH CALM</span>
    </div>
  </section>

  <section class="card card--back-green">
    <div class="wordmark wordmark--large">
      <span class="wordmark__name">KERNOVA</span>
      <span class="wordmark__tagline">MAKING TECH CALM</span>
    </div>
  </section>

  <section class="card card--back-tech">
    <div class="tech-backdrop" role="img" aria-label="Abstract blue digital backdrop with glowing light rings and binary code"></div>
    <div class="wordmark wordmark--large">
      <span class="wordmark__name">KERNOVA</span>
      <span class="wordmark__tagline">MAKING TECH CALM</span>
    </div>
  </section>
</body>
</html>
```